Yoga/movement guide/teacher for adult yoga practice and kid yoga

What is the positioning or mission statement of your company? to guide individuals in a yoga-based safe and sustainable movement practice applicable to all ages and body types. Currently my focus is working with children in daycare and school settings, but my goal is to expand into private yoga practice for adults, and potentially as part of rented space in studios. I hope to find a way to work with children AND adults (so would love for logo to be appealing to both), but current focus is with children based on need and demand in the community. yoga for children also compliments my backround as a pediatrician/neonatologist, and I greatly miss interacting with children. I also want to emphasize a yoga/movement practice that is focused more on what one feels internally through movement. NOT what one looks like asthetically. I believe in removing all mirrors from yoga/movement practice. It should be an experience of movement/poses/yoga through appropriate cueing and education. It is not about the details of how far the knee should bend, or how high the leg should be. Focusing on foudation first, core, then core engagement and ultimately expression of poses/movements. A focus on strength, stability and mobility, not just flexibility, which is the common perception/association with yoga. I also want individuals to learn to be an advocate of their own health. Through guidance, I hope for individuals to connect with their body so they know themselves so well to be able to advocate for themselves in the modern healthcare world. This internal experience and connection is so essential in a world where modern medicine has become a business and it is all about making a dollar. the connection with patients is lost, and individuals need to learn to empower themselves and through their new found voice to be able to articulate what is wrong.<br/>Does your company have a tagline or slogan that should be included with the logo? "Move With Your Inner Glow"<br/>What do you hope your company can be known for? Accessible yoga for a sustained practice. A guided movement practice where one gains information and knowledge of oneself through a mind/body connection. For one feel good physically with a new awaraness of their internal radiance that exists in all beings. Physical rejuvenation egnites a light and increases energy to flow through the physical body, which ultimately tranlates into works of kindness for others and out in the world. <br/>What color palettes might you prefer? why? love the colors currently chosen<br/>Where will the logo be primarily used? initially business cards, but hopefully future websites, t-shirts, and potentially local magazine adds. Also starting with a small couple of banners for community events in the area. I currently practice as a nomad out of my car :)<br/>Are there any elements you would prefer to see in the logo? Movement. A modern depiction of a human body/figure practicing movement. Hoping to avoid a stereotypical yoga pose per say, just because I want to people to think of it more of a movement practice with yoga roots. Modern yoga. There are elements of breathing and connecting with oneself through the flow of breath and movement, but I do not focus on the meditative/cerebral aspect of the yoga practice. What I teach is almost reaching a meditative state through movement. I personally don't practice, nor resonate with just seated meditation. just not my thing :)<br/>In your opinion, what defines a well-designed logo? curiosity. enough info for individuals to think they know what it means, but want to know more. invokes curiosity, but not too abstract. Reproducible. not too complicated. I want also to invoke a community feel, so a design that appeals to all people within a community. <br/>What is your preference in reference to icons, typography, spokespeople (characters), etc.? modern design. I love the idea of a logo for my purposes, to invoke a sense of movement from within. So not too static. <br/>What words or icons must be included in the logo? movement with yoga roots. <br/>What logos do you like and why? A representation, but not exact. I think some ambiguity is intriguing for others, and also memorable. I want it to be an artistic representation of movement/yoga<br/>What logos do you dislike and why? too busy, too loud. <br/>In your opinion, what is the primary purpose for a logo? association<br/>Who is the primary target audience? (who is most likely to use your services/product?) Children and their parents, but ultimately to expand into teaching adults. I even have aspirations of prenatal and post-natal yoga. Potentially incorporating infants. <br/>Who currently uses your product the most? n/a (working in schools/daycare currently. It is currently all volunteer)<br/>Are you pleased with the range of people your company serves? n/a<br/>Are you looking to expand, modify, or completely change your target audience? or will it remain the same? yes! expand into an adult audience. <br/>How do you plan to focus on your target audience? currently by working through schools and daycares. hopefully ultimately through after school care programs and then offering kid yoga in an existing yoga studio (working on this with Q Studio in Ridgeland, currently)<br/>What are your main forms of advertising? word of mouth, schools, daycares. Happy kids talking to their parents about the yoga class they took and happy teachers :)<br/>How do most customers find out about your company?<br/>Which gender are you targeting? All genders! However, with kid yoga, often the maternal individual in the child's life is more involved with decision making as far as extracurricular activities

Target Market(s)

individuals and families interested in wellness and feeling great

Contact Information for Business Card

Dana Whitford
Yoga Instructor
RYT-200, RCYT

certified yoga teacher for adults and children

Colors

Designer to choose colors to be used in the design.

Requirements
Must have
• "Move With Your Inner Glow"
Nice to have
• logo with same colors

```html
<!DOCTYPE html>
<html lang="en">
<head>
<meta charset="utf-8">
<title>Glowfield Studios – Business Card</title>
<link href="https://fonts.googleapis.com/css2?family=Arimo:wght@400;700&family=Oswald:wght@300&display=swap" rel="stylesheet">
<style>
  :root {
    --backdrop: #8c8c8c;
    --teal: #63cad0;
    --sun: #f5d93b;
    --charcoal: #252525;
    --stone: #9a9a9a;
    --white: #ffffff;
  }
  html, body {
    margin: 0;
    padding: 0;
    width: 1200px;
    height: 802px;
    overflow: hidden;
    background: var(--backdrop);
  }
  .canvas {
    position: relative;
    width: 1200px;
    height: 802px;
  }
  .card {
    position: absolute;
    top: 274px;
    width: 444px;
    height: 265px;
    overflow: hidden;
    box-shadow: 2px 3px 6px rgba(0,0,0,0.35);
  }
  .card--front {
    left: 152px;
    background: var(--teal);
    font-family: "Arimo", Arial, sans-serif;
    color: var(--white);
  }
  .card--back {
    left: 624px;
    background: var(--charcoal);
  }
  .front__panel {
    position: absolute;
    top: 0;
    right: 0;
    width: 90px;
    height: 100%;
    background: var(--sun);
  }
  .contact {
    position: absolute;
    left: 31px;
    top: 60px;
  }
  .contact__name {
    margin: 0;
    font-size: 17px;
    font-weight: 700;
    line-height: 1;
    letter-spacing: 0.2px;
  }
  .contact__role {
    margin: 2px 0 0;
    font-size: 12.5px;
    line-height: 1.1;
  }
  .contact__list {
    list-style: none;
    margin: 16px 0 0;
    padding: 0;
    font-size: 12.5px;
    line-height: 16px;
  }
  .contact__list li {
    display: flex;
    align-items: center;
    gap: 4px;
  }
  .contact__icon {
    width: 10px;
    height: 10px;
    fill: var(--white);
  }
  .contact__address {
    margin: 14px 0 0 2px;
    font-size: 12.5px;
    line-height: 16px;
    font-style: normal;
  }
  .brand__dot {
    position: absolute;
    left: 151px;
    top: 87px;
    width: 90px;
    height: 90px;
    border-radius: 50%;
    background: var(--sun);
  }
  .brand__name {
    position: absolute;
    left: 250px;
    top: 118px;
    margin: 0;
    font-family: "Arimo", Arial, sans-serif;
    font-weight: 400;
    font-size: 22px;
    line-height: 1;
    color: var(--stone);
    white-space: nowrap;
  }
  .tagline {
    position: absolute;
    left: 214px;
    top: 206px;
    margin: 0;
    font-family: "Oswald", "Arial Narrow", sans-serif;
    font-weight: 300;
    font-size: 9px;
    line-height: 1;
    letter-spacing: 1.6px;
    text-transform: uppercase;
    color: var(--teal);
    white-space: nowrap;
  }
</style>
</head>
<body>
<main class="canvas">
  <section class="card card--front" aria-label="Business card front">
    <div class="front__panel"></div>
    <div class="contact">
      <h1 class="contact__name">DANA WHITFORD</h1>
      <p class="contact__role">Yoga Instructor</p>
      <ul class="contact__list">
        <li><svg class="contact__icon" viewBox="0 0 10 10" aria-hidden="true"><path d="M1 3 Q5 0 9 3 L8 4.5 L6.5 3.8 L6.5 3 Q5 2.5 3.5 3 L3.5 3.8 L2 4.5 Z M2.5 5 H7.5 L8.5 9 H1.5 Z"/></svg>044-555 210 348</li>
        <li><svg class="contact__icon" viewBox="0 0 10 10" aria-hidden="true"><path d="M0.5 2 H9.5 V8.5 H0.5 Z M1.2 2.7 L5 5.6 L8.8 2.7" stroke="#63cad0" stroke-width="0.8"/></svg>hello@glowfieldyoga.com</li>
        <li><svg class="contact__icon" viewBox="0 0 10 10" aria-hidden="true"><circle cx="5" cy="5" r="4.5"/><path d="M2.5 3.5 Q4 2.5 4.5 4 Q6 5 5 7 M6.5 2 Q7.5 3.5 7 5" stroke="#63cad0" stroke-width="0.9" fill="none"/></svg>www.glowfieldyoga.com</li>
      </ul>
      <address class="contact__address">18 Linden Walk, Ridgeland<br>39157, United States</address>
    </div>
  </section>

  <section class="card card--back" aria-label="Business card back">
    <span class="brand__dot" aria-hidden="true"></span>
    <p class="brand__name">Glowfield Studios</p>
    <p class="tagline">Move With Your Inner Glow</p>
  </section>
</main>
</body>
</html>
```